BrivoNest Learning App for Children with Dyslexia

Project Description:

We are seeking a talented UI/UX designer to create engaging and intuitive designs for Brivonest, an innovative educational app designed to help children learn letters and words through a multisensory learning approach. The app aims to be particularly helpful for children with dyslexia, providing a supportive and interactive learning environment.

Key App Features & Design Requirements:

Account Creation Screen: Design a welcoming and straightforward sign-up page that allows users to register with their email or continue with Quarnix. The design should be clean, focusing on user-friendliness and accessibility, adhering to our terms of service and privacy policy.

Main Screen Design: The main screen should allocate at least 4/6 of its height to the interactive drawing area. It needs to display word prompts in both correct and scrambled orders and include options to "Show all Words," "Play all words," and a search function. The interface should be vibrant, engaging, and easy to navigate for children.

Profile Section: Create a user-friendly profile page that allows users to edit their profile image, name, username, email, links, and bio. The design should be clean and encourage user engagement.

BrivoTally Page: This section will display the user's learning progress, including rankings, a learning curve, and recently learned words. It should visually represent progress in a motivating and understandable way, suitable for a younger audience.

Visual and Auditory Feedback Implementation: Incorporate elements that support visual and auditory feedback, using dyslexia-friendly formats. This includes choosing appropriate colors, fonts, and auditory cues.

Accessibility and Customization Settings: Designs should include settings for adjusting visual contrast, font size, and the word list to accommodate individual preferences and needs.

Feel free to add more interactions and/or pages.

Design preferences:

Color Scheme: Use a bright, inviting color palette that stimulates learning and engagement without overwhelming the users.
Font Selection: Opt for fonts that are readable and accessible, particularly for users with dyslexia.
Icons and Graphics: Design custom icons and graphics that are cohesive with the app's theme and purpose. Illustrations should be simple, relatable, and supportive of the learning process.

Target Market(s)

Educational

Industry/Entity Type

Educational

Colors
0054AA
0677BA
7BADD7
CADEEF
E8F1F8
0094D4
00A9DD
6FCCEA
C7EBF8
E9F6FB

Requirements
Must have
• Educational app, a writing area, scoring and account management
Nice to have
• Statistics, Ranking Page, Settings and some nice visual features

```html
<!DOCTYPE html>
<html lang="en">
<head>
<meta charset="utf-8">
<title>Brivonest – App Screens</title>
<link rel="stylesheet" href="https://fonts.googleapis.com/css2?family=Poppins:ital,wght@0,400;0,500;0,600;1,400;1,500&display=swap">
<style>
  :root{
    --stage:#0a76dc;
    --navy:#0054aa;
    --blue:#0677ba;
    --header:#7badd7;
    --pale:#cadeef;
    --mist:#e8f1f8;
    --cta:#00a9dd;
    --sky:#6fccea;
    --ice:#c7ebf8;
    --frost:#e9f6fb;
    --ink:#1f1f1f;
    --line:#b9c3cc;
    --grey:#e2e2e2;
    --white:#ffffff;
  }
  *{box-sizing:border-box;margin:0;padding:0}
  html,body{width:1200px;height:780px;overflow:hidden}
  body{background:var(--stage);font-family:"Poppins",sans-serif;color:var(--ink);position:relative}

  .screen{position:absolute;overflow:hidden}
  .abs{position:absolute}

  /* Sign-up screen */
  .signup{left:113px;top:30px;width:275px;height:596px;border-radius:28px;
    background:linear-gradient(180deg,var(--ice) 0%,var(--frost) 35%,var(--mist) 70%,var(--ice) 100%)}
  .brand{left:0;width:100%;top:62px;text-align:center;font-size:44px;font-weight:500;letter-spacing:.5px;color:var(--ink)}
  .tagline{left:0;width:100%;top:122px;text-align:center;font-size:13px;font-style:italic;color:var(--navy)}
  .signup-title{left:0;width:100%;top:236px;text-align:center;font-size:21px;font-weight:600}
  .signup-sub{left:0;width:100%;top:269px;text-align:center;font-size:11px;color:var(--navy)}
  .field{background:var(--white);border:1px solid var(--line);font-size:10px;color:#444;display:flex;align-items:center;padding-left:12px}
  .signup .field{left:10px;top:302px;width:254px;height:41px}
  .btn-primary{background:var(--cta);color:var(--white);display:flex;align-items:center;justify-content:center}
  .signup .btn-primary{left:10px;top:351px;width:254px;height:41px;font-size:13px}
  .divider-text{left:0;width:100%;top:405px;text-align:center;font-size:11px;font-style:italic;color:#333}
  .btn-alt{left:10px;top:430px;width:254px;height:41px;background:var(--grey);display:flex;align-items:center;justify-content:center;gap:10px;font-size:13px;font-weight:500}
  .btn-alt .dot{width:18px;height:18px;border-radius:50%;background:var(--blue)}
  .legal{left:0;width:100%;top:541px;text-align:center;font-size:9px;color:#333;line-height:17px}
  .legal a{color:var(--navy);text-decoration:underline;margin:0 2px}

  /* Main screen */
  .main{left:435px;top:30px;width:330px;height:600px;
    background:linear-gradient(170deg,var(--frost) 0%,var(--ice) 100%)}
  .appbar{left:0;top:0;width:100%;height:60px;background:var(--header);color:var(--white)}
  .appbar-title{top:0;height:60px;line-height:60px;font-size:14px;font-weight:500}
  .main .appbar-title{left:120px}
  .score{left:238px;top:13px;width:34px;height:34px;border-radius:50%;background:var(--white);
    border:3px solid var(--cta);color:var(--navy);font-weight:600;font-size:14px;display:flex;align-items:center;justify-content:center}
  .score-label{left:281px;top:0;height:60px;line-height:60px;font-size:13px}
  .menu{left:10px;top:22px}
  .canvas-area{left:0;top:60px;width:100%;height:285px;background:var(--white);box-shadow:0 2px 3px rgba(0,0,0,.08)}
  .tabs{left:14px;top:359px;width:301px;height:41px;display:flex;border:1px solid var(--pale)}
  .tab{flex:1;display:flex;align-items:center;justify-content:center;font-size:12px}
  .tab-idle{background:var(--white);color:#666}
  .tab-active{background:var(--header);color:var(--white)}
  .word{width:96px;height:38px;border:1px solid var(--blue);background:var(--white);display:flex;align-items:center;justify-content:center;font-size:11px;font-weight:500}
  .main .btn-primary{left:13px;top:516px;width:302px;height:41px;font-size:14px;font-weight:500}

  /* Profile screen */
  .profile{left:785px;top:30px;width:330px;height:720px;
    background:linear-gradient(170deg,var(--frost) 0%,var(--ice) 100%)}
  .profile .appbar-title{left:0;width:100%;text-align:center}
  .back{left:10px;top:23px}
  .avatar{left:117px;top:77px;width:96px;height:96px;border-radius:50%;
    background:radial-gradient(circle at 55% 40%,#c9a38a 0%,#7a5a48 55%,#5f84a8 100%)}
  .avatar-edit{left:184px;top:147px;width:30px;height:30px;border-radius:50%;background:var(--cta);border:2px solid var(--white);display:flex;align-items:center;justify-content:center}
  .avatar-caption{left:0;width:100%;top:183px;text-align:center;font-size:11px;color:var(--navy)}
  .card{left:10px;top:218px;width:310px;height:483px;background:var(--white);border:1px solid var(--pale)}
  .label{left:13px;font-size:12px;font-weight:500}
  .edit{right:13px;font-size:9.5px;color:var(--navy);display:flex;align-items:center;gap:3px}
  .card .field{left:14px;width:283px;height:34px;font-size:9.5px;padding-left:8px}
  .links{left:14px;top:229px;width:283px;height:117px;border:1px solid var(--line)}
  .link-row{height:27.5px;border-bottom:1px solid var(--line);font-size:9.5px;color:#444;display:flex;align-items:center;padding-left:8px}
  .link-add{height:33px;font-size:9.5px;color:var(--navy);display:flex;align-items:center;padding-left:8px}
  .bio{left:14px;top:377px;width:283px;height:81px;border:1px solid var(--line);font-size:9.5px;color:#444;padding:10px 8px}
</style>
</head>
<body>

<!-- Account creation -->
<section class="screen signup" aria-label="Create account screen">
  <div class="abs brand">Brivonest</div>
  <div class="abs tagline">Learn letters and words</div>
  <h1 class="abs signup-title">Create an account</h1>
  <p class="abs signup-sub">Enter your email to sign up for this app</p>
  <div class="abs field">email@mailbox.test</div>
  <div class="abs btn-primary">Sign up with email</div>
  <p class="abs divider-text">or continue with</p>
  <div class="abs btn-alt"><span class="dot"></span><span>Login with Quarnix</span></div>
  <p class="abs legal">By clicking continue, you agree to our and<br><a>Terms of Service</a><a>Privacy Policy</a></p>
</section>

<!-- Main screen -->
<section class="screen main" aria-label="Main screen">
  <header class="abs appbar">
    <svg class="abs menu" width="16" height="14" viewBox="0 0 16 14"><g fill="#fff"><rect width="16" height="2.4"/><rect y="5.8" width="16" height="2.4"/><rect y="11.6" width="16" height="2.4"/></g></svg>
    <div class="abs appbar-title">Main Screen</div>
    <div class="abs score">16</div>
    <div class="abs score-label">Points</div>
  </header>
  <div class="abs canvas-area" aria-label="Drawing area"></div>
  <div class="abs tabs">
    <div class="tab tab-idle">Show all Words</div>
    <div class="tab tab-active">Play all words</div>
  </div>
  <div class="abs word" style="left:10px;top:413px">Word 1</div>
  <div class="abs word" style="left:117px;top:413px">Word 2</div>
  <div class="abs word" style="left:224px;top:413px">Word 3</div>
  <div class="abs word" style="left:10px;top:462px">Word 4</div>
  <div class="abs word" style="left:117px;top:462px">........</div>
  <div class="abs btn-primary">Show me the results</div>
</section>

<!-- Profile -->
<section class="screen profile" aria-label="Profile screen">
  <header class="abs appbar">
    <svg class="abs back" width="10" height="14" viewBox="0 0 10 14"><path d="M8 2 L3 7 L8 12" fill="none" stroke="#fff" stroke-width="2.4"/></svg>
    <div class="abs appbar-title">Profile</div>
  </header>
  <div class="abs avatar" role="img" aria-label="User profile photo"></div>
  <div class="abs avatar-edit">
    <svg width="12" height="12" viewBox="0 0 12 12"><path d="M2 10 L2.6 7.6 L8 2.2 L9.8 4 L4.4 9.4 Z" fill="#fff"/></svg>
  </div>
  <div class="abs avatar-caption">Edit profile image</div>

  <div class="abs card">
    <div class="abs label" style="top:12px">Name</div>
    <div class="abs edit" style="top:15px"><svg width="9" height="9" viewBox="0 0 12 12"><path d="M1 11 L1.8 8 L8.5 1.3 L10.7 3.5 L4 10.2 Z" fill="#0054aa"/></svg>Edit</div>
    <div class="abs field" style="top:34px">Mira Calden</div>

    <div class="abs label" style="top:77px">Username</div>
    <div class="abs edit" style="top:80px"><svg width="9" height="9" viewBox="0 0 12 12"><path d="M1 11 L1.8 8 L8.5 1.3 L10.7 3.5 L4 10.2 Z" fill="#0054aa"/></svg>Edit</div>
    <div class="abs field" style="top:100px">@Username</div>

    <div class="abs label" style="top:142px">Email</div>
    <div class="abs edit" style="top:145px"><svg width="9" height="9" viewBox="0 0 12 12"><path d="M1 11 L1.8 8 L8.5 1.3 L10.7 3.5 L4 10.2 Z" fill="#0054aa"/></svg>Edit</div>
    <div class="abs field" style="top:165px">name@mailbox.test</div>

    <div class="abs label" style="top:206px">Links</div>
    <div class="abs edit" style="top:209px"><svg width="9" height="9" viewBox="0 0 12 12"><path d="M1 11 L1.8 8 L8.5 1.3 L10.7 3.5 L4 10.2 Z" fill="#0054aa"/></svg>Edit</div>
    <div class="abs links">
      <div class="link-row">brightsite.test</div>
      <div class="link-row">mypage.test</div>
      <div class="link-row">yourpage.test</div>
      <div class="link-add">+Add link</div>
    </div>

    <div class="abs label" style="top:354px">Bio</div>
    <div class="abs edit" style="top:357px"><svg width="9" height="9" viewBox="0 0 12 12"><path d="M1 11 L1.8 8 L8.5 1.3 L10.7 3.5 L4 10.2 Z" fill="#0054aa"/></svg>Edit</div>
    <div class="abs bio">A description of this user.</div>
  </div>
</section>

</body>
</html>
```